Business Card for Coastal Tundrabridge Advisory

We need a business card for Coastal Tundrabridge Advisory. The company website address is provided below. The company logo is attached. We provide specialized permafrost services to the mining, transportation, and oil & gas industries. The card should be prepared for:
Matthias Korhonen, PhD.
Coastal Tundrabridge Advisory
PO Box 418259
Quillwater, Alaska 99642
Direct: +1-907-555-0143
Email: mkorhonen@tundrabridgeadvisory.example
Website: www.coastaltundrabridgeadvisory.example

```html
<!DOCTYPE html>
<html lang="en">
<head>
<meta charset="utf-8">
<title>Coastal Tundrabridge Advisory — Business Card</title>
<link rel="stylesheet" href="https://fonts.googleapis.com/css2?family=Open+Sans:ital,wght@1,700&family=PT+Sans+Narrow:wght@700&family=Montserrat:wght@600&display=swap">
<style>
  :root {
    --page-bg: #ececec;
    --card-white: #ffffff;
    --ink: #1e1e1e;
    --ink-soft: #3a3a3a;
    --frame: #6f6f6f;
    --rule: #9a9a9a;
    --dark-1: #383838;
    --dark-2: #262626;
    --logo-ink: #e6e6e6;
  }
  * { margin: 0; padding: 0; box-sizing: border-box; }
  html, body { width: 1200px; height: 1199px; overflow: hidden; }
  body { background: var(--page-bg); position: relative; font-family: "PT Sans Narrow", sans-serif; }

  .card {
    position: absolute;
    left: 237px;
    width: 726px;
    height: 412px;
    border-radius: 38px;
    overflow: hidden;
  }
  .card--front { top: 156px; background: var(--card-white); }
  .card--back  { top: 645px; background: var(--dark-2); }

  .card__frame { position: absolute; inset: 0; }

  .holder {
    position: absolute;
    right: calc(726px - 340px);
    top: 108px;
    text-align: right;
    color: var(--ink-soft);
    font-family: "Open Sans", sans-serif;
    font-style: italic;
    font-weight: 700;
  }
  .holder__name { font-size: 21px; letter-spacing: -0.4px; line-height: 1.2; }
  .holder__title { font-size: 9.5px; margin-top: 4px; }

  .divider {
    position: absolute;
    left: 361px; top: 124px;
    width: 1.5px; height: 132px;
    background: var(--rule);
  }

  .contacts { position: absolute; left: 382px; top: 144px; list-style: none; }
  .contacts__item {
    display: flex; align-items: center; gap: 8px;
    height: 26.7px;
    font-size: 15px; color: var(--ink);
  }
  .contacts__icon { width: 17px; height: 17px; flex: none; }

  .address {
    position: absolute;
    left: 0; right: 0; top: 349px;
    text-align: center;
    font-size: 15px; line-height: 22px; color: var(--ink);
  }

  .back__texture {
    position: absolute; inset: 0;
    background: linear-gradient(160deg, var(--dark-1) 0%, var(--dark-2) 55%, #1f1f1f 100%);
  }
  .back__brand {
    position: absolute;
    left: 300px; top: 238px;
    font-family: "Montserrat", sans-serif;
    font-weight: 600;
    font-size: 22px;
    letter-spacing: 3px;
    line-height: 30px;
    text-transform: uppercase;
    color: var(--logo-ink);
  }
</style>
</head>
<body>

<section class="card card--front" aria-label="Business card front">
  <svg class="card__frame" width="726" height="412" viewBox="0 0 726 412" aria-hidden="true">
    <path d="M148 375 H41 Q19 375 19 353 V39 Q19 17 41 17 H687 Q709 17 709 39 V353 Q709 375 687 375 H575"
          fill="none" stroke="var(--frame)" stroke-width="2.2"/>
  </svg>

  <div class="holder">
    <p class="holder__name">Matthias Korhonen, PhD</p>
    <p class="holder__title">Founder &amp; Director</p>
  </div>

  <div class="divider"></div>

  <ul class="contacts">
    <li class="contacts__item">
      <svg class="contacts__icon" viewBox="0 0 20 20" aria-hidden="true"><circle cx="10" cy="10" r="8.6" fill="none" stroke="#444" stroke-width="1.4"/><path d="M7 5.5l1.6 2.2-1 1.2a6 6 0 0 0 3.5 3.5l1.2-1 2.2 1.6-.9 1.6c-3.6-.3-7.2-3.9-7.5-7.5z" fill="#444"/></svg>
      <span>+1-907-555-0143</span>
    </li>
    <li class="contacts__item">
      <svg class="contacts__icon" viewBox="0 0 20 20" aria-hidden="true"><circle cx="10" cy="10" r="8.6" fill="none" stroke="#444" stroke-width="1.4"/><rect x="7" y="4.5" width="6" height="11" rx="1.2" fill="none" stroke="#444" stroke-width="1.3"/><circle cx="10" cy="13.5" r=".8" fill="#444"/></svg>
      <span>(907) 555 0143</span>
    </li>
    <li class="contacts__item">
      <svg class="contacts__icon" viewBox="0 0 20 20" aria-hidden="true"><circle cx="10" cy="10" r="8.6" fill="none" stroke="#444" stroke-width="1.4"/><rect x="5" y="6.5" width="10" height="7" rx="1" fill="#444"/><path d="M5.5 7.2l4.5 3.4 4.5-3.4" fill="none" stroke="#fff" stroke-width="1"/></svg>
      <span>mkorhonen@tundrabridgeadvisory.example</span>
    </li>
    <li class="contacts__item">
      <svg class="contacts__icon" viewBox="0 0 20 20" aria-hidden="true"><circle cx="10" cy="10" r="8.6" fill="none" stroke="#444" stroke-width="1.4"/><circle cx="10" cy="10" r="5" fill="none" stroke="#444" stroke-width="1.1"/><ellipse cx="10" cy="10" rx="2.2" ry="5" fill="none" stroke="#444" stroke-width="1"/><path d="M5 10h10" stroke="#444" stroke-width="1"/></svg>
      <span>www.coastaltundrabridgeadvisory.example</span>
    </li>
  </ul>

  <p class="address">PO Box 418259<br>Quillwater, Alaska 99642</p>
</section>

<section class="card card--back" aria-label="Business card back">
  <div class="back__texture" role="img" aria-label="Dark charcoal background with a repeating tone-on-tone brand name pattern"></div>
  <p class="back__brand">Coastal Tundrabridge<br>Advisory</p>
</section>

</body>
</html>
```